Brellwick Partners, LLC Stationary

Brellwick Partners, LLC is a new financial planning and consulting company. We are looking for designs on business cards, letterhead, envelopes, and anything else that would be useful. Our preference for business card design is two sided. We are looking for a professional and clean look with incorporating the logo and patriotic feel. Thank you to all who participate and good luck!

```html
<!DOCTYPE html>
<html lang="en">
<head>
<meta charset="utf-8">
<title>Brellwick Partners, LLC – Business Card</title>
<link rel="stylesheet" href="https://fonts.googleapis.com/css2?family=Michroma&family=Montserrat:wght@400;500;600&display=swap">
<style>
  :root {
    --navy: #0f3d6e;
    --red: #d2363c;
    --ink: #4a4f57;
    --muted: #8b9099;
    --paper: #ffffff;
    --backdrop: #e9e6e1;
    --faint: #eef0f4;
  }
  * { box-sizing: border-box; margin: 0; padding: 0; }
  html, body { width: 1200px; height: 950px; overflow: hidden; }
  body {
    background: var(--backdrop);
    font-family: "Montserrat", Arial, sans-serif;
    position: relative;
  }
  .card {
    position: absolute;
    left: 250px;
    width: 700px;
    height: 400px;
    border-radius: 4px;
    box-shadow: 0 10px 28px rgba(0,0,0,.18);
    overflow: hidden;
  }
  .card-front { top: 45px; background: var(--paper); }
  .card-back { top: 495px; background: var(--navy); }

  .front-accent {
    position: absolute; right: -90px; top: -60px;
    width: 340px; height: 340px; border-radius: 50%;
    background: var(--faint);
  }
  .front-band {
    position: absolute; left: 0; top: 44px;
    width: 64px; height: 64px;
    background: var(--navy);
  }
  .brand {
    position: absolute; left: 86px; top: 50px;
  }
  .brand-name {
    font-family: "Michroma", Arial, sans-serif;
    color: var(--navy);
    font-size: 22px;
    line-height: 1.2;
    letter-spacing: 1px;
    text-transform: uppercase;
    white-space: nowrap;
  }
  .brand-tagline {
    margin-top: 8px;
    font-size: 9.5px;
    letter-spacing: 2.4px;
    color: var(--muted);
    text-transform: uppercase;
  }
  .person {
    position: absolute; left: 86px; top: 138px;
  }
  .person-name {
    font-family: "Michroma", Arial, sans-serif;
    color: var(--navy);
    font-size: 19px;
    letter-spacing: 1px;
    text-transform: uppercase;
  }
  .person-title {
    margin-top: 4px;
    font-family: "Michroma", Arial, sans-serif;
    color: var(--red);
    font-size: 14px;
    text-transform: uppercase;
    letter-spacing: .5px;
  }
  .contact {
    position: absolute; left: 86px; top: 212px;
    list-style: none;
    color: var(--ink);
    font-size: 13px;
    line-height: 1.5;
  }
  .contact-address { margin-bottom: 8px; }
  .contact-row { display: flex; align-items: center; gap: 10px; }
  .contact-row svg { width: 13px; height: 13px; fill: var(--ink); flex: none; }

  .back-brand {
    position: absolute; left: 0; right: 0; top: 160px;
    display: flex; align-items: center; justify-content: center; gap: 14px;
  }
  .back-mark { width: 22px; height: 22px; background: var(--paper); }
  .back-name {
    font-family: "Michroma", Arial, sans-serif;
    color: var(--paper);
    font-size: 24px;
    letter-spacing: 1px;
    text-transform: uppercase;
  }
  .back-web {
    position: absolute; left: 40px; bottom: 34px;
    color: var(--paper);
    font-size: 13px;
    letter-spacing: 1.5px;
  }
</style>
</head>
<body>
  <section class="card card-front" aria-label="Business card front">
    <div class="front-accent" aria-hidden="true"></div>
    <div class="front-band" aria-hidden="true"></div>
    <div class="brand">
      <p class="brand-name">Brellwick Partners, LLC</p>
      <p class="brand-tagline">Financial Planning and Consulting</p>
    </div>
    <div class="person">
      <p class="person-name">Daniel Harlow</p>
      <p class="person-title">CEO/Founder</p>
    </div>
    <ul class="contact">
      <li class="contact-address">1422 Willowmere Road<br>Juneau, Alaska 99801</li>
      <li class="contact-row">
        <svg viewBox="0 0 16 16" aria-hidden="true"><path d="M3.5 1l3 3-1.8 1.8a9 9 0 0 0 5.5 5.5L12 9.5l3 3-2 2C6.5 14.5 1.5 9.5 1.5 3z"/></svg>
        555 310 4827
      </li>
      <li class="contact-row">
        <svg viewBox="0 0 16 16" aria-hidden="true"><path d="M4 0h8a1 1 0 0 1 1 1v14a1 1 0 0 1-1 1H4a1 1 0 0 1-1-1V1a1 1 0 0 1 1-1zm1 2v10h6V2zm3 11a1 1 0 1 0 0 2 1 1 0 0 0 0-2z"/></svg>
        555 310 4828
      </li>
      <li class="contact-row">
        <svg viewBox="0 0 16 16" aria-hidden="true"><path d="M0 3h16v10H0zm1.5 1.2V12h13V4.2L8 9z"/></svg>
        hello@brellwick.com
      </li>
      <li class="contact-row">
        <svg viewBox="0 0 16 16" aria-hidden="true"><path d="M8 0a8 8 0 1 0 0 16A8 8 0 0 0 8 0zm0 1.5c1 1.3 1.7 3.2 1.8 5.7H6.2C6.3 4.7 7 2.8 8 1.5zM1.6 8.8h3c.1 2.2.7 4 1.5 5.3a6.5 6.5 0 0 1-4.5-5.3zm0-1.6a6.5 6.5 0 0 1 4.5-5.3C5.3 3.2 4.7 5 4.6 7.2zm4.6 1.6h3.6c-.1 2.5-.8 4.4-1.8 5.7-1-1.3-1.7-3.2-1.8-5.7zm5.2 0h3a6.5 6.5 0 0 1-4.5 5.3c.8-1.3 1.4-3.1 1.5-5.3zm0-1.6c-.1-2.2-.7-4-1.5-5.3a6.5 6.5 0 0 1 4.5 5.3z"/></svg>
        www.brellwickpartners.com
      </li>
    </ul>
  </section>

  <section class="card card-back" aria-label="Business card back">
    <div class="back-brand">
      <span class="back-mark" aria-hidden="true"></span>
      <p class="back-name">Brellwick Partners, LLC</p>
    </div>
    <p class="back-web">www.brellwickpartners.com</p>
  </section>
</body>
</html>
```